Business Card for my New Brokerage

Looking to get a business card design for my new Real Estate Brokerage.
I want it with Picture, Phone Number, Email, Website, Office Address
Name and Designation. Please add logo too.

Target Market(s)

Real Estate Investors or Home Buyers

Industry/Entity Type

Real Estate

Contact Information for Business Card

Name, Email, Phone Number, website, email, office address

Colors
EB3D1F
EC4F4E
F09395
F8D3D4
FCEDEE

Requirements
Must have
• Minimalistic, Clean, Modern, Photo
Nice to have
• White and Red Colors

```html
<!DOCTYPE html>
<html lang="en">
<head>
<meta charset="utf-8">
<title>Ember Realty Inc – Business Card</title>
<link rel="stylesheet" href="https://fonts.googleapis.com/css2?family=Montserrat:wght@400;500;600;800&display=swap">
<style>
  :root {
    --red: #e00000;
    --ink: #1c1c1c;
    --grey: #8a8a8a;
    --paper: #fdfdfd;
    --page: #ffffff;
    --photo-light: #f1f1f1;
    --photo-mid: #cfcfcf;
  }
  * { box-sizing: border-box; margin: 0; padding: 0; }
  html, body {
    width: 687px; height: 1200px; overflow: hidden;
    background: var(--page);
    font-family: "Montserrat", sans-serif;
  }
  .sheet {
    position: relative; width: 687px; height: 1200px;
    display: flex; flex-direction: column; align-items: center; justify-content: center;
    gap: 60px;
  }
  .card {
    position: relative; width: 600px; height: 343px;
    background: var(--paper);
    box-shadow: 0 6px 14px rgba(0,0,0,.28);
    overflow: hidden;
  }

  /* Front */
  .front-band { position: absolute; inset: 0; }
  .brand-name {
    position: absolute; left: 46px; top: 92px;
    font-size: 44px; font-weight: 600; line-height: 1.1;
    color: var(--ink); white-space: nowrap;
  }
  .front-web {
    position: absolute; left: 46px; top: 274px;
    font-size: 20px; font-weight: 500; color: var(--grey); letter-spacing: .3px;
  }

  /* Back */
  .agent-photo {
    position: absolute; right: 0; top: 0; width: 250px; height: 343px;
    background:
      linear-gradient(to right, var(--paper) 0%, rgba(253,253,253,0) 30%),
      radial-gradient(ellipse at 55% 45%, var(--photo-mid) 0%, var(--photo-light) 65%, var(--paper) 100%);
  }
  .agent-name {
    position: absolute; left: 38px; top: 44px;
    font-size: 40px; line-height: 1; color: var(--ink); letter-spacing: .5px; white-space: nowrap;
  }
  .agent-first { color: var(--red); font-weight: 800; }
  .agent-last { font-weight: 400; }
  .agent-role {
    position: absolute; left: 38px; top: 96px;
    font-size: 18px; font-weight: 500; color: var(--ink); letter-spacing: 1.2px;
  }
  .contact-tab {
    position: absolute; left: 0; top: 170px;
    width: 62px; height: 144px;
    background: var(--red); border-radius: 0 14px 14px 0;
  }
  .contact-tab svg { position: absolute; inset: 0; }
  .contact-list {
    position: absolute; left: 75px; top: 181px;
    list-style: none; font-size: 15.5px; font-weight: 500; color: var(--ink);
    letter-spacing: .5px; line-height: 20px;
  }
  .contact-list li { margin-bottom: 14px; }
  .contact-list li.address { margin-bottom: 8px; }
</style>
</head>
<body>
<main class="sheet">

  <section class="card card-front" aria-label="Business card front">
    <svg class="front-band" viewBox="0 0 600 343" aria-hidden="true">
      <polygon points="306,343 600,41 600,124 382,343" fill="var(--red)"/>
    </svg>
    <p class="brand-name">Ember Realty Inc</p>
    <p class="front-web">www.emberrealtyinc.com</p>
  </section>

  <section class="card card-back" aria-label="Business card back">
    <div class="agent-photo" role="img" aria-label="Portrait photo of the agent in a grey blazer with arms crossed"></div>
    <h1 class="agent-name"><span class="agent-first">DANIEL</span> <span class="agent-last">HART</span></h1>
    <p class="agent-role">REAL ESTATE BROKERAGE</p>

    <div class="contact-tab">
      <svg viewBox="0 0 62 144" aria-hidden="true" fill="none" stroke="#fff" stroke-width="1.4" stroke-linecap="round" stroke-linejoin="round">
        <line x1="10" y1="40" x2="62" y2="40" stroke="rgba(255,255,255,.35)"/>
        <line x1="10" y1="76" x2="62" y2="76" stroke="rgba(255,255,255,.35)"/>
        <line x1="10" y1="110" x2="62" y2="110" stroke="rgba(255,255,255,.35)"/>
        <path d="M37 16c-2-2-3-2-4-1l-1 1c-1 1-3 0-5-2s-3-4-2-5l1-1c1-1 1-2-1-4s-3-2-4-1l-1 1c-2 2 0 7 4 11s9 6 11 4l1-1c1-1 1-2-1-3z" transform="translate(4,4)"/>
        <path d="M42 58c0 5-6 10-6 10s-6-5-6-10a6 6 0 0 1 12 0z"/>
        <circle cx="36" cy="58" r="2.2"/>
        <rect x="29" y="86" width="15" height="11" rx="1"/>
        <path d="M29 87l7.5 6 7.5-6M29 97l5.5-5M44 97l-5.5-5"/>
        <circle cx="36" cy="126" r="7.5"/>
        <ellipse cx="36" cy="126" rx="3.4" ry="7.5"/>
        <path d="M28.5 126h15M30 122h12M30 130h12"/>
      </svg>
    </div>

    <ul class="contact-list">
      <li>(555) 010 2468</li>
      <li class="address">Lorem Ipsum is simply<br>dummy text</li>
      <li>info@emberrealtyinc.com</li>
      <li>www.emberrealtyinc.com</li>
    </ul>
  </section>

</main>
</body>
</html>
```